Stationery Design Project for Nimbora, Chicago

Nimbora, a street parking application which helps car drivers find a street parking spot by offering an ideal path along which to look for parking. This path is calculated by our algorithm based on data (e.g. historical data, baseball games schedule, etc.). Along this path the driver will find a spot and will also save 70% of the search time. Customer we target is reg. between 21 and 45 yo.

We envision something young, fresh, bright and original. Slightly abstract maybe. It should represent the idea and elements of finding street parking in the city, e.g. car(s), parking spot, people, city, etc. (just ideas!).

Logo is attached.

Requirement:
- Business Cards (2 Sided Full Color CMYK)
- Letterhead (1 Sided Full Color CMYK)
- Envelope (1 Sided Full Color CMYK)
- Sticker (1 Sided Full Color CMYK), round with a 2inch diameter.

Reason: We're starting to get more and more designs and need more time to look into all of them. Very exciting!! Thanks to everybody!

Hi all, we're in the process of selecting our favs. Though choices!!! Really good submissions. Will keep you posted and sorry for the delay.

Target Market(s)

Car drivers and owners between 21 and 45

Industry/Entity Type

Parking

Requirements
Must have
• Sticker should be round and include company URL nimbora.com and the new logo which we will attach soon.
Should not have
• Should not be too serious or boring.

```html
<!DOCTYPE html>
<html lang="en">
<head>
<meta charset="utf-8">
<title>Nimbora Business Card</title>
<link rel="stylesheet" href="https://fonts.googleapis.com/css2?family=Open+Sans:wght@400;600;700&display=swap">
<style>
  :root {
    --page-bg: #e9e9e9;
    --card-white: #ffffff;
    --ink-dark: #1f1f1f;
    --ink-grey: #555555;
    --ink-body: #222222;
    --blue-deep: #2b3c96;
    --blue-bright: #1a7bcc;
    --blue-logo: #2052b8;
    --stripe-black: #111111;
    --back-center: #5a5a5a;
    --back-edge: #000000;
    --navy-text: #14204d;
  }
  * { margin: 0; padding: 0; box-sizing: border-box; }
  html, body { width: 954px; height: 1200px; overflow: hidden; }
  body {
    background: var(--page-bg);
    font-family: "Open Sans", Arial, sans-serif;
    position: relative;
  }
  .card {
    position: absolute;
    left: 74px;
    width: 796px;
    height: 455px;
    border-radius: 28px;
    overflow: hidden;
    box-shadow: 0 4px 10px rgba(0,0,0,0.25);
  }
  .card-front { top: 112px; background: var(--card-white); }
  .card-back {
    top: 657px;
    background: radial-gradient(ellipse at 50% 40%, var(--back-center) 0%, #2a2a2a 45%, var(--back-edge) 80%);
  }
  .card-band { position: absolute; left: 0; top: 0; width: 796px; height: 455px; }

  .brand-mark {
    position: absolute;
    left: 106px; top: 43px;
    width: 156px; height: 156px;
    border-radius: 50%;
    background: var(--blue-logo);
  }
  .brand-name {
    position: absolute;
    left: 290px; top: 52px;
    font-size: 104px;
    font-weight: 600;
    color: var(--ink-dark);
    letter-spacing: -1px;
    line-height: 1;
  }
  .person {
    position: absolute;
    left: 0; width: 796px; top: 212px;
    text-align: center;
    color: var(--ink-grey);
    font-weight: 700;
  }
  .person-name { font-size: 24px; }
  .person-sep { font-size: 20px; font-weight: 400; margin: 0 6px; }
  .person-role { font-size: 19px; }

  .contact-phones {
    position: absolute;
    right: 432px; top: 285px;
    text-align: right;
    font-size: 18px;
    line-height: 32px;
    color: var(--ink-body);
  }
  .contact-phones b { font-weight: 700; }
  .contact-divider {
    position: absolute;
    left: 377px; top: 286px;
    width: 1.5px; height: 54px;
    background: var(--ink-body);
  }
  .contact-address {
    position: absolute;
    left: 388px; top: 285px;
    font-size: 18px;
    line-height: 27px;
    color: var(--ink-body);
  }
  .front-web {
    position: absolute;
    left: 0; width: 796px; top: 410px;
    text-align: center;
    font-size: 18px;
    color: #ffffff;
  }
  .front-web b { font-weight: 700; }
  .front-web .sep { margin: 0 8px; }

  .back-mark {
    position: absolute;
    left: 335px; top: 135px;
    width: 126px; height: 126px;
    border-radius: 50%;
    background: var(--blue-logo);
  }
  .back-web {
    position: absolute;
    left: 0; width: 796px; top: 407px;
    text-align: center;
    font-size: 21px;
    letter-spacing: 6px;
    color: var(--navy-text);
  }
</style>
</head>
<body>
  <section class="card card-front" aria-label="Business card front">
    <svg class="card-band" viewBox="0 0 796 455" aria-hidden="true">
      <defs>
        <linearGradient id="band-blue" x1="0" x2="1" y1="0" y2="0">
          <stop offset="0" stop-color="var(--blue-deep)"/>
          <stop offset="0.25" stop-color="var(--blue-bright)"/>
          <stop offset="0.75" stop-color="var(--blue-bright)"/>
          <stop offset="1" stop-color="var(--blue-deep)"/>
        </linearGradient>
      </defs>
      <path d="M0 400 Q398 350 796 400 L796 410 Q398 360 0 410 Z" fill="var(--stripe-black)"/>
      <path d="M0 414 Q398 364 796 414 L796 455 L0 455 Z" fill="url(#band-blue)"/>
    </svg>
    <div class="brand-mark" aria-hidden="true"></div>
    <div class="brand-name">nimbora</div>
    <div class="person">
      <span class="person-name">Your Name</span><span class="person-sep">|</span><span class="person-role">Designation</span>
    </div>
    <div class="contact-phones">
      <div><b>t</b> : 123-456-7890</div>
      <div><b>m</b> : 123-456-7890</div>
    </div>
    <div class="contact-divider"></div>
    <div class="contact-address">
      <div>City Name, Street Name</div>
      <div>State Name, Country Code</div>
    </div>
    <div class="front-web"><b>e</b> : name@website.com<span class="sep">|</span><b>w</b> : www.website.com</div>
  </section>

  <section class="card card-back" aria-label="Business card back">
    <svg class="card-band" viewBox="0 0 796 455" aria-hidden="true">
      <defs>
        <linearGradient id="band-blue-back" x1="0" x2="1" y1="0" y2="0">
          <stop offset="0" stop-color="var(--blue-deep)"/>
          <stop offset="0.25" stop-color="var(--blue-bright)"/>
          <stop offset="0.75" stop-color="var(--blue-bright)"/>
          <stop offset="1" stop-color="var(--blue-deep)"/>
        </linearGradient>
      </defs>
      <path d="M0 382 Q398 342 796 382 L796 391 Q398 351 0 391 Z" fill="#ffffff"/>
      <path d="M0 394 Q398 354 796 394 L796 455 L0 455 Z" fill="url(#band-blue-back)"/>
    </svg>
    <div class="back-mark" aria-hidden="true"></div>
    <div class="back-web">www.website.com</div>
  </section>
</body>
</html>
```